New Webpage for High Class Expert Witness Services Company

We are looking for a minimalist design for a webpage that just has our logo and an entry form offer to connect with one of our Liaisons.
The entry form should just ask for Name, Email, Contact Info and Description of Project.

Company Name is: The Marlowe Crest Advisory Services

Number of Pages Required

1 page

```html
<!DOCTYPE html>
<html lang="en">
<head>
<meta charset="utf-8">
<title>The Marlowe Crest Advisory Services — Connect with a Liaison</title>
<link rel="stylesheet" href="https://fonts.googleapis.com/css2?family=Cinzel:wght@600;700&family=Inter:wght@400;500&display=swap">
<style>
  :root{
    --ink:#0f0f11;
    --panel:#15161a;
    --stone-dark:#121213;
    --stone-mid:#262627;
    --gold:#c4a86a;
    --gold-line:#b59a5e;
    --white:#ffffff;
    --silver:#d6d6d6;
    --rule:#4a4a4a;
    --button-text:#1a1a1a;
  }
  *{box-sizing:border-box;margin:0;padding:0}
  html,body{width:934px;height:1200px;overflow:hidden;background:var(--ink)}
  body{position:relative;font-family:"Inter",Arial,sans-serif;color:var(--white)}

  .site-header{position:absolute;left:0;top:0;width:934px;height:82px;background:var(--ink);
    border-bottom:1px solid var(--rule);display:flex;align-items:center;justify-content:center}
  .brand-name{font-family:"Cinzel",Georgia,serif;font-weight:600;color:var(--silver);
    text-align:center;line-height:1.05;letter-spacing:.04em}
  .site-header .brand-name{font-size:20px}

  .hero{position:absolute;left:0;top:83px;width:934px;height:354px;text-align:center}
  .stone-texture{position:absolute;inset:0;
    background:radial-gradient(ellipse at 30% 20%,var(--stone-mid),transparent 60%),
               radial-gradient(ellipse at 75% 70%,#1f1f20,transparent 60%),var(--stone-dark)}
  .hero-content{position:relative;padding-top:88px}
  .hero-title{font-family:"Cinzel",Georgia,serif;font-weight:700;font-size:31px;line-height:39px;
    color:var(--silver);letter-spacing:.01em}
  .hero-lead{margin-top:20px;font-size:13.5px}
  .btn{display:inline-flex;align-items:center;justify-content:center;background:var(--gold);
    color:var(--button-text);font-family:"Inter",Arial,sans-serif;font-weight:500;font-size:15px;
    width:168px;height:43px;border:none;letter-spacing:.01em}
  .hero .btn{margin-top:21px}

  .contact{position:absolute;left:0;top:437px;width:934px;height:542px;background:var(--panel)}
  .contact-title{position:absolute;left:0;top:120px;width:934px;text-align:center;
    font-family:"Cinzel",Georgia,serif;font-weight:700;font-size:38px;letter-spacing:.01em}
  .field-label{position:absolute;font-size:13.5px;font-weight:500}
  .field{position:absolute;border:1px solid var(--gold-line);border-radius:6px;background:transparent}
  .contact .btn{position:absolute;left:473px;top:406px}

  .site-footer{position:absolute;left:0;top:979px;width:934px;height:221px;border-top:1px solid var(--gold-line)}
  .site-footer .brand-name{position:absolute;left:0;top:50px;width:934px;font-size:26px}
  .copyright{position:absolute;left:100px;top:146px;width:734px;height:41px;display:flex;
    align-items:center;justify-content:center;font-size:12.5px;color:var(--button-text);
    background:linear-gradient(90deg,transparent 0%,var(--gold) 14%,var(--gold) 86%,transparent 100%)}
</style>
</head>
<body>
  <header class="site-header">
    <div class="brand-name">Marlowe Crest<br>Advisory Services</div>
  </header>

  <section class="hero">
    <div class="stone-texture" role="img" aria-label="Dark charcoal marble texture background"></div>
    <div class="hero-content">
      <h1 class="hero-title">EXPERT WITNESS SUPPORT. DELIVERED<br>WITH PRECISION</h1>
      <p class="hero-lead">Connect with a liaison to discuss your case requirements.</p>
      <span class="btn">GET STARTED</span>
    </div>
  </section>

  <section class="contact">
    <h2 class="contact-title">CONNECT WITH A LIAISON</h2>

    <label class="field-label" style="left:124px;top:204px">Full Name</label>
    <div class="field" style="left:125px;top:238px;width:324px;height:42px"></div>

    <label class="field-label" style="left:124px;top:293px">Email Address</label>
    <div class="field" style="left:125px;top:323px;width:324px;height:43px"></div>

    <label class="field-label" style="left:124px;top:380px">Contact Number</label>
    <div class="field" style="left:125px;top:409px;width:324px;height:43px"></div>

    <label class="field-label" style="left:473px;top:204px">Project Description</label>
    <div class="field" style="left:473px;top:238px;width:324px;height:127px"></div>

    <span class="btn">SEND NOW</span>
  </section>

  <footer class="site-footer">
    <div class="stone-texture" role="img" aria-label="Dark charcoal marble texture background"></div>
    <div class="brand-name">Marlowe Crest<br>Advisory Services</div>
    <div class="copyright">Copyright 2026, The Marlowe Crest Advisory Services. All Rights Reserved</div>
  </footer>
</body>
</html>
```